Social Event Calendar for real estate ad

I need a one page - 8 1/2 x 11 card (front and back) designed to include a list of events and images. The design should look somewhat tropical and friendly utilizing the color Aqua Blue. I am a real estate broker in West Palm Beach, Florida.

Target Market(s)

Adult homeowners age 30-80 of Florida homes primarily in the West Palm Beach, Florida historic homes market. The purpose of the marketing piece is to provide interesting content on the social events occurring within the next 6 months in the area. The ad should portray the sender as an expert in the neighborhood. The call to action will be for the reader to contact the sender of the ad to determine the value of the reader's home.

Industry/Entity Type

Real Estate

Font styles to use
Other font styles liked:
• Helvetica

Colors
0092cd
00a990
e567a6

Requirements
Must have
• Must have a calendar listing of events similar to the screenshot provided but fitting 10 events for January and 10 for February.

```html
<!DOCTYPE html>
<html lang="en">
<head>
<meta charset="utf-8">
<title>Social Events Listing – West Palm Beach Real Estate</title>
<link rel="stylesheet" href="https://fonts.googleapis.com/css2?family=Arimo:ital,wght@0,400;0,700;1,400&family=Oswald:wght@700&family=Open+Sans:wght@700&display=swap">
<style>
  :root {
    --header-green: #3fd676;
    --date-green: #3fd676;
    --date-pink: #e155d9;
    --title-pink: #e24fda;
    --title-outline: #3b2a48;
    --footer-pink: #e24fe0;
    --water-light: #33c9ec;
    --water-deep: #1a86e4;
    --arrow-light: #f3f5f6;
    --arrow-shade: #c5cacd;
    --photo-light: #a9cbe6;
    --photo-deep: #5d8fbd;
    --ink: #1d1d1d;
    --white: #ffffff;
  }
  html, body {
    margin: 0;
    padding: 0;
    overflow: hidden;
  }
  body {
    width: 848px;
    height: 1200px;
    position: relative;
    font-family: "Arimo", Helvetica, Arial, sans-serif;
  }
  .header-band {
    position: absolute;
    left: 0; top: 0;
    width: 848px; height: 114px;
    background: var(--header-green);
  }
  .agent-portrait {
    position: absolute;
    left: 0; top: 0;
    width: 94px; height: 113px;
    background: linear-gradient(180deg, #8e9aa2, #6f7c85);
    border: 1px solid #555;
    box-sizing: border-box;
  }
  .tagline {
    position: absolute;
    margin: 0;
    color: var(--white);
    font-weight: 700;
    font-size: 34px;
    line-height: 1;
    white-space: nowrap;
  }
  .tagline--primary { left: 132px; top: 12px; }
  .tagline--secondary { right: 27px; top: 63px; }
  .water-backdrop {
    position: absolute;
    left: 0; top: 114px;
    width: 848px; height: 1053px;
    background: linear-gradient(160deg, var(--water-light) 0%, #28b0ec 45%, var(--water-deep) 100%);
  }
  .listing-title {
    position: absolute;
    left: 0; top: 126px;
    width: 862px;
    margin: 0;
    text-align: center;
    font-size: 56px;
    font-weight: 400;
    color: var(--title-pink);
    -webkit-text-stroke: 1.3px var(--title-outline);
    line-height: 1;
  }
  .event-board {
    position: absolute;
    left: 0; top: 0;
    width: 848px; height: 1200px;
  }
  .event-text {
    font-family: "Arimo", Helvetica, Arial, sans-serif;
    font-style: italic;
    font-size: 20px;
    fill: var(--ink);
  }
  .date-day {
    font-family: "Oswald", "Arial Narrow", sans-serif;
    font-weight: 700;
    font-size: 42px;
    fill: var(--white);
  }
  .date-month {
    font-family: "Oswald", "Arial Narrow", sans-serif;
    font-weight: 700;
    font-size: 23px;
    fill: var(--white);
  }
  .contact-bar {
    position: absolute;
    left: 0; top: 1167px;
    width: 848px; height: 33px;
    background: var(--footer-pink);
    display: flex;
    align-items: center;
    justify-content: center;
    font-family: "Open Sans", Helvetica, Arial, sans-serif;
    font-weight: 700;
    font-size: 15px;
    color: #1a1a1a;
    white-space: nowrap;
  }
  .contact-bar .sep { margin: 0 9px; }
</style>
</head>
<body>
  <header class="header-band">
    <div class="agent-portrait" role="img" aria-label="Agent portrait photo"></div>
    <p class="tagline tagline--primary">“Your #1 Real Estate Agent”</p>
    <p class="tagline tagline--secondary">“For West Palm Beach, Florida”</p>
  </header>

  <div class="water-backdrop" role="img" aria-label="Splashing aqua water background photo"></div>

  <h1 class="listing-title">Social Events Listing</h1>

  <svg class="event-board" viewBox="0 0 848 1200" xmlns="http://www.w3.org/2000/svg">
    <defs>
      <linearGradient id="arrowFace" x1="0" y1="0" x2="0" y2="1">
        <stop offset="0" stop-color="var(--arrow-light)"/>
        <stop offset="1" stop-color="var(--arrow-shade)"/>
      </linearGradient>
      <linearGradient id="photoFill" x1="0" y1="0" x2="0" y2="1">
        <stop offset="0" stop-color="var(--photo-light)"/>
        <stop offset="1" stop-color="var(--photo-deep)"/>
      </linearGradient>
    </defs>

    <g class="photo-column photo-column--right">
      <circle role="img" aria-label="Local landscape photo" cx="697" cy="286" r="83" fill="url(#photoFill)"/>
      <circle role="img" aria-label="Local landscape photo" cx="697" cy="457" r="83" fill="url(#photoFill)"/>
      <circle role="img" aria-label="Local landscape photo" cx="697" cy="624" r="83" fill="url(#photoFill)"/>
      <circle role="img" aria-label="Local landscape photo" cx="697" cy="791" r="83" fill="url(#photoFill)"/>
      <circle role="img" aria-label="Local landscape photo" cx="697" cy="958" r="83" fill="url(#photoFill)"/>
    </g>

    <g class="photo-column photo-column--left">
      <circle role="img" aria-label="Local landscape photo" cx="132" cy="402" r="83" fill="url(#photoFill)"/>
      <circle role="img" aria-label="Local landscape photo" cx="132" cy="569" r="83" fill="url(#photoFill)"/>
      <circle role="img" aria-label="Local landscape photo" cx="132" cy="735" r="83" fill="url(#photoFill)"/>
      <circle role="img" aria-label="Local landscape photo" cx="132" cy="902" r="83" fill="url(#photoFill)"/>
      <circle role="img" aria-label="Local landscape photo" cx="132" cy="1069" r="83" fill="url(#photoFill)"/>
    </g>

    <g class="event-row event-row--right" transform="translate(0,280)">
      <polygon points="340,0 556,0 611,40 556,79 340,79" fill="url(#arrowFace)"/>
      <rect x="265" y="0" width="75" height="79" fill="var(--date-pink)"/>
      <text class="date-day" x="302" y="45" text-anchor="middle">01</text>
      <text class="date-month" x="302" y="72" text-anchor="middle">DEC</text>
      <text class="event-text" x="360" y="29">open house event</text>
      <text class="event-text" x="360" y="54">palm beach</text>
    </g>
    <g class="event-row event-row--left" transform="translate(0,359)">
      <polygon points="275,0 484,0 484,79 275,79 220,40" fill="url(#arrowFace)"/>
      <rect x="484" y="0" width="76" height="79" fill="var(--date-green)" stroke="#1e5a38" stroke-width="1"/>
      <text class="date-day" x="522" y="45" text-anchor="middle">03</text>
      <text class="date-month" x="522" y="72" text-anchor="middle">DEC</text>
      <text class="event-text" x="302" y="31">your event listing</text>
      <text class="event-text" x="302" y="56">venue, address</text>
    </g>
    <g class="event-row event-row--right" transform="translate(0,440)">
      <polygon points="340,0 556,0 611,40 556,79 340,79" fill="url(#arrowFace)"/>
      <rect x="265" y="0" width="75" height="79" fill="var(--date-pink)"/>
      <text class="date-day" x="302" y="45" text-anchor="middle">08</text>
      <text class="date-month" x="302" y="72" text-anchor="middle">DEC</text>
      <text class="event-text" x="360" y="29">open house event</text>
      <text class="event-text" x="360" y="54">palm beach</text>
    </g>
    <g class="event-row event-row--left" transform="translate(0,519)">
      <polygon points="275,0 484,0 484,79 275,79 220,40" fill="url(#arrowFace)"/>
      <rect x="484" y="0" width="76" height="79" fill="var(--date-green)" stroke="#1e5a38" stroke-width="1"/>
      <text class="date-day" x="522" y="45" text-anchor="middle">10</text>
      <text class="date-month" x="522" y="72" text-anchor="middle">DEC</text>
      <text class="event-text" x="302" y="31">your event listing</text>
      <text class="event-text" x="302" y="56">venue, address</text>
    </g>
    <g class="event-row event-row--right" transform="translate(0,599)">
      <polygon points="340,0 556,0 611,40 556,79 340,79" fill="url(#arrowFace)"/>
      <rect x="265" y="0" width="75" height="79" fill="var(--date-pink)"/>
      <text class="date-day" x="302" y="45" text-anchor="middle">12</text>
      <text class="date-month" x="302" y="72" text-anchor="middle">DEC</text>
      <text class="event-text" x="360" y="29">open house event</text>
      <text class="event-text" x="360" y="54">palm beach</text>
    </g>
    <g class="event-row event-row--left" transform="translate(0,678)">
      <polygon points="275,0 484,0 484,79 275,79 220,40" fill="url(#arrowFace)"/>
      <rect x="484" y="0" width="76" height="79" fill="var(--date-green)" stroke="#1e5a38" stroke-width="1"/>
      <text class="date-day" x="522" y="45" text-anchor="middle">15</text>
      <text class="date-month" x="522" y="72" text-anchor="middle">DEC</text>
      <text class="event-text" x="302" y="31">your event listing</text>
      <text class="event-text" x="302" y="56">venue, address</text>
    </g>
    <g class="event-row event-row--right" transform="translate(0,758)">
      <polygon points="340,0 556,0 611,40 556,79 340,79" fill="url(#arrowFace)"/>
      <rect x="265" y="0" width="75" height="79" fill="var(--date-pink)"/>
      <text class="date-day" x="302" y="45" text-anchor="middle">18</text>
      <text class="date-month" x="302" y="72" text-anchor="middle">DEC</text>
      <text class="event-text" x="360" y="29">open house event</text>
      <text class="event-text" x="360" y="54">palm beach</text>
    </g>
    <g class="event-row event-row--left" transform="translate(0,834)">
      <polygon points="275,0 484,0 484,79 275,79 220,40" fill="url(#arrowFace)"/>
      <rect x="484" y="0" width="76" height="79" fill="var(--date-green)" stroke="#1e5a38" stroke-width="1"/>
      <text class="date-day" x="522" y="45" text-anchor="middle">21</text>
      <text class="date-month" x="522" y="72" text-anchor="middle">DEC</text>
      <text class="event-text" x="302" y="31">your event listing</text>
      <text class="event-text" x="302" y="56">venue, address</text>
    </g>
    <g class="event-row event-row--right" transform="translate(0,912)">
      <polygon points="340,0 556,0 611,40 556,79 340,79" fill="url(#arrowFace)"/>
      <rect x="265" y="0" width="75" height="79" fill="var(--date-pink)"/>
      <text class="date-day" x="302" y="45" text-anchor="middle">24</text>
      <text class="date-month" x="302" y="72" text-anchor="middle">DEC</text>
      <text class="event-text" x="360" y="29">open house event</text>
      <text class="event-text" x="360" y="54">palm beach</text>
    </g>
    <g class="event-row event-row--left" transform="translate(0,993)">
      <polygon points="275,0 484,0 484,79 275,79 220,40" fill="url(#arrowFace)"/>
      <rect x="484" y="0" width="76" height="79" fill="var(--date-green)" stroke="#1e5a38" stroke-width="1"/>
      <text class="date-day" x="522" y="45" text-anchor="middle">25</text>
      <text class="date-month" x="522" y="72" text-anchor="middle">DEC</text>
      <text class="event-text" x="302" y="31">your event listing</text>
      <text class="event-text" x="302" y="56">venue, address</text>
    </g>
  </svg>

  <footer class="contact-bar">
    <span>Direct Line: 000.000.0000</span><span class="sep">|</span>
    <span>Email: name@realestate.com</span><span class="sep">|</span>
    <span>Website: www.yourwebsite.com</span>
  </footer>
</body>
</html>
```